K SPIRES Business Card Design

Need a business card design for K Spires, we're a tower company - our main scope of work is to upgrade cellular sites: swap antennas, install new coax, fiber, replace mounts, etc. Mostly tower work.

would like to see a sharp business card design with our logo either on background or with tower image on the background - something describing our field not only in words but in images.

Target Market(s)

USA

Industry/Entity Type

Business

Contact Information for Business Card

Tarnek Obliva
Operations Manager
K Spires LLC

cell 555-318-2094
tarnek@k-spires-example.com

4185 Wexbridge Commerce Pkwy, Suite D
Norcross, GA, 30571

Requirements
Must have
• some tower related design
Nice to have
• some tower or cellular antennas on the background, if possible to compliment our logo...

```html
<!DOCTYPE html>
<html lang="en">
<head>
<meta charset="utf-8">
<title>K Spires Business Card</title>
<link rel="stylesheet" href="https://fonts.googleapis.com/css2?family=PT+Sans:wght@400;700&display=swap">
<style>
  :root {
    --page-bg: #e9e6e1;
    --card-white: #ffffff;
    --card-black: #0d0d0d;
    --brand-blue: #2e3192;
    --brand-green: #2e8b45;
    --shadow: rgba(0, 0, 0, 0.18);
  }
  * { box-sizing: border-box; margin: 0; padding: 0; }
  html, body {
    width: 1200px;
    height: 1200px;
    overflow: hidden;
    background: var(--page-bg);
    font-family: "PT Sans", Arial, sans-serif;
  }
  .card {
    position: absolute;
    left: 180px;
    width: 840px;
    height: 480px;
    box-shadow: 0 10px 30px var(--shadow);
    overflow: hidden;
  }
  .card--back {
    top: 70px;
    background: var(--card-black);
    display: flex;
    align-items: center;
    justify-content: center;
  }
  .card--front {
    top: 650px;
    background: var(--card-white);
  }
  .tower-backdrop {
    position: absolute;
    left: 300px;
    top: 40px;
    width: 240px;
    height: 400px;
    background: radial-gradient(ellipse at 50% 55%, rgba(46, 49, 146, 0.28), rgba(46, 139, 69, 0.10) 55%, rgba(13, 13, 13, 0) 75%);
  }
  .brand-name {
    position: relative;
    font-family: "PT Sans", Arial, sans-serif;
    font-weight: 700;
    color: var(--brand-blue);
    letter-spacing: 1px;
    line-height: 1;
  }
  .card--back .brand-name { font-size: 96px; }
  .card--front .brand-name {
    position: absolute;
    right: 90px;
    top: 190px;
    font-size: 88px;
  }
  .accent-shapes {
    position: absolute;
    inset: 0;
    width: 840px;
    height: 480px;
  }
  .holder {
    position: absolute;
    left: 112px;
    top: 30px;
  }
  .holder-name {
    font-size: 32px;
    font-weight: 700;
    color: var(--brand-blue);
    line-height: 1.1;
  }
  .holder-title {
    font-size: 22px;
    color: var(--brand-green);
    margin-top: 4px;
  }
  .contact {
    position: absolute;
    left: 40px;
    top: 178px;
    font-size: 21px;
    line-height: 1.35;
    color: var(--brand-blue);
    list-style: none;
  }
  .contact-label { color: var(--brand-green); }
</style>
</head>
<body>
  <section class="card card--back" aria-label="Card back">
    <div class="tower-backdrop" role="img" aria-label="Faint cell tower with antennas behind the company name"></div>
    <div class="brand-name">K Spires</div>
  </section>

  <section class="card card--front" aria-label="Card front">
    <svg class="accent-shapes" viewBox="0 0 840 480" aria-hidden="true">
      <polygon points="0,30 78,30 58,70 0,70" fill="var(--brand-blue)"/>
      <polygon points="84,30 100,30 80,70 64,70" fill="var(--brand-green)"/>
      <polygon points="0,362 430,362 410,402 0,402" fill="var(--brand-green)"/>
      <polygon points="410,402 840,402 840,452 384,452" fill="var(--brand-blue)"/>
    </svg>

    <div class="holder">
      <div class="holder-name">Tarnek Obliva</div>
      <div class="holder-title">Operations Manager</div>
    </div>

    <ul class="contact">
      <li>4185 Wexbridge Commerce Pkwy, Suite D</li>
      <li>Norcross, GA, 30571</li>
      <li><span class="contact-label">c:</span> 555-318-2094</li>
      <li><span class="contact-label">e:</span> tarnek@k-spires-example.com</li>
    </ul>

    <div class="brand-name">K Spires</div>
  </section>
</body>
</html>
```